Graphic Design Project

ok I have the artwork for my presentation folder, and I have the text to put on the folder, I need you to apply text to the folder and the single sheets, so inside the artwork is pictures to use, text to use. thank you so much ask me as many questions as you need
Updates

my girl forgot to upload the mock ups of the presentation folder and single sheets, my apologies please check updated files

Hey Guys this is a eazy project the artwork is done, the text is done, the pictures are done!, all you have to do is assemble the project, I even have mock up pictures of how project looks finished, I have made the money good so that you would not pass on this project because it is not that creative of a job!

Target Market(s)

Dr's and patients

Industry/Entity Type

Graphic Design

Requirements
Must have
• use the single sheet artwork to make as many single sheets as you need to use all of the text supplied
Should not have
• do not make this, so professional looking that it does not appeal to the patients

```html
<!DOCTYPE html>
<html lang="en">
<head>
<meta charset="utf-8">
<title>TruePath Counseling – Folder Spread</title>
<link rel="stylesheet" href="https://fonts.googleapis.com/css2?family=Tinos:wght@400;700&display=swap">
<style>
  :root {
    --backdrop: #e9e4dc;
    --paper: #ffffff;
    --brown: #744b27;
    --brown-text: #8a4f21;
    --grey-panel: #d1d1d3;
    --grey-name: #707072;
    --beige: #d8d0c1;
    --ink: #111111;
    --light-ink: #f4ede4;
  }
  * { margin: 0; padding: 0; box-sizing: border-box; }
  html, body { width: 1200px; height: 1000px; overflow: hidden; background: var(--backdrop); }
  body { position: relative; font-family: "Tinos", "Times New Roman", serif; }
  .spread-art { position: absolute; inset: 0; }
  .intro { position: absolute; left: 628px; top: 168px; width: 470px; color: var(--ink); }
  .intro-title { font-size: 27px; font-weight: 700; line-height: 34px; margin-bottom: 16px; }
  .brand-pro { color: var(--brown-text); }
  .brand-care { color: var(--grey-name); }
  .intro p { font-size: 11px; line-height: 12.6px; margin-bottom: 13px; }
  .intro p b { font-weight: 700; }
  .ethics {
    position: absolute; left: 111px; top: 670px; width: 250px;
    color: var(--light-ink); font-size: 9.3px; line-height: 10.6px;
  }
  .ethics p + p { margin-top: 10px; }
  .folder-name {
    position: absolute; left: 430px; top: 700px;
    display: flex; align-items: center; gap: 8px;
    font-size: 24px; color: var(--brown-text); font-weight: 400;
  }
  .folder-name .dot { width: 30px; height: 30px; border-radius: 50%; background: var(--grey-name); }
</style>
</head>
<body>
  <svg class="spread-art" width="1200" height="1000" viewBox="0 0 1200 1000" aria-hidden="false">
    <defs>
      <linearGradient id="lawnTone" x1="0" y1="0" x2="1" y2="1">
        <stop offset="0" stop-color="#6f9a4a"/>
        <stop offset="0.5" stop-color="#a7b48c"/>
        <stop offset="1" stop-color="#5e8a3a"/>
      </linearGradient>
      <linearGradient id="autumnTone" x1="0" y1="0" x2="1" y2="1">
        <stop offset="0" stop-color="#e8d7b6"/>
        <stop offset="0.55" stop-color="#b89a78"/>
        <stop offset="1" stop-color="#6b4a30"/>
      </linearGradient>
    </defs>
    <rect class="folder-paper" x="103" y="147" width="1016" height="677" fill="var(--paper)"/>
    <path class="top-band" fill="var(--brown)" d="M118 147 L545 147 L515 245 Q508 266 485 261 L140 166 Q118 160 118 147 Z"/>
    <path class="photo-seniors-lawn" role="img" aria-label="Photo of four smiling seniors lying in a circle on grass" fill="url(#lawnTone)"
      d="M103 195 L470 288 Q500 298 493 325 L412 630 Q405 650 385 645 L103 578 Z"/>
    <path class="lower-band" fill="var(--brown)" d="M103 595 L370 665 Q395 672 390 695 L358 824 L103 824 Z"/>
    <path class="grey-panel" fill="var(--grey-panel)"
      d="M548 147 L1050 147 L1119 172 L1119 390 L1075 595 Q1066 614 1045 607 L500 466 Q480 459 485 438 Z"/>
    <path class="beige-panel" fill="var(--beige)"
      d="M470 500 Q476 484 498 490 L1030 628 Q1050 635 1045 656 L1005 824 L418 824 L400 765 Q396 752 399 740 Z"/>
    <path class="photo-senior-couple" role="img" aria-label="Photo of a smiling senior couple outdoors among autumn leaves" fill="url(#autumnTone)"
      d="M608 518 L1030 628 Q1050 635 1045 656 L1005 824 L608 824 Z"/>
    <path class="edge-beige" fill="var(--beige)" d="M1100 470 L1119 460 L1119 690 L1080 680 Q1062 674 1066 655 Z"/>
    <path class="edge-grey" fill="var(--grey-panel)" d="M1040 705 L1119 700 L1119 824 L1020 824 Z"/>
  </svg>

  <section class="intro">
    <h1 class="intro-title"><span class="brand-pro">True</span><span class="brand-care">Path</span> Counseling</h1>
    <p><b><span class="brand-pro">True</span><span class="brand-care">Path</span> Counseling</b> will provide education, assessments, prevention and screening for those individuals with chronic pain and substance use disorders.</p>
    <p><b><span class="brand-pro">True</span><span class="brand-care">Path</span> Counseling</b> is a proactive addiction counseling center dedicated to addressing health issues in an integrated manner by working with pain management physicians to offer opioid education to prevent substance use and misuse disorders to their patients. Many pain management clinics and primary care physicians are interested in reducing risk to their patients and practice from opioid misuse and increasing quality care for their patients. Physicians are excited to have a service like <b><span class="brand-pro">True</span><span class="brand-care">Path</span> Counseling</b> to provide education and screening services for their patients.</p>
    <p><b><span class="brand-pro">True</span><span class="brand-care">Path</span> Counseling</b> services are provided by highly trained and caring professionals who are experienced in working in all areas of patient education, prevention and care.</p>
    <p><b><span class="brand-pro">True</span><span class="brand-care">Path</span> Counseling</b> is a resource for pain management clinics and primary care physicians to educate, assess and provide prevention and counseling to patients to reduce the risk of substance use disorders.</p>
    <p><b><span class="brand-pro">True</span><span class="brand-care">Path</span> Counseling</b> will always place the patient’s interest first and endeavor to earn and maintain the patient’s trust from the very beginning.</p>
  </section>

  <section class="ethics">
    <p>TruePath’s dedicated and experienced counselors radiate a contagious interest in the life of our patients, within an intimate, caring environment that engenders transformative learning.<br>We are determined to emphasize high ethical standards in all aspects of our counseling center.</p>
    <p>We will hold our reputation and the integrity of our counseling center before the community in which we serve.<br>From an ethical standpoint, our patients will feel that our office is a “safe and warm” place to be.<br>At TruePath Counseling, We are committed to educating and informing your patients and making a difference in their lives and the lives of their loved ones.</p>
  </section>

  <div class="folder-name"><span class="dot"></span><span>TruePath Counseling</span></div>
</body>
</html>
```